Local Roofing/Construction company business needs new biz card design

We need a new business card design, current cards are from the start of this operation and generic at best. We are a local Construction Company (General Contractor) with a majority of our work originating from insurance claims-exterior finish work is the main focus (Roofs-Siding-Gutters etc). Heavily involved with homeowners and the low ball offers they receive from insurance company's after a insurable event takes place. I have attached some of our original logo file(s) below.

```html
<!DOCTYPE html>
<html lang="en">
<head>
<meta charset="utf-8">
<title>Halden Build Co — Business Card</title>
<link rel="stylesheet" href="https://fonts.googleapis.com/css2?family=Exo+2:wght@400;500;700&display=swap">
<style>
  :root {
    --ink-dark: #0d1e22;
    --ink-black: #050a0b;
    --brand-green: #2fd87a;
    --paper: #ffffff;
    --text: #1f2326;
    --rule: #d4d7d8;
    --stage: #b3b3b3;
  }
  * { box-sizing: border-box; margin: 0; padding: 0; }
  html, body { width: 1093px; height: 1200px; overflow: hidden; }
  body {
    background: var(--stage);
    font-family: "Exo 2", sans-serif;
    position: relative;
  }

  .card {
    position: absolute;
    left: 265px;
    width: 580px;
    height: 356px;
    border-radius: 26px;
    overflow: hidden;
  }

  /* Front */
  .card-front { top: 226px; background: var(--paper); }
  .top-band {
    position: absolute; left: 0; top: 0; width: 100%; height: 18px;
    background: var(--ink-dark);
    border-bottom: 6px solid var(--ink-black);
  }
  .brand-tab {
    position: absolute; left: 37px; top: 0; width: 246px; height: 320px;
    background: var(--ink-black);
    border-radius: 0 0 26px 26px;
    padding: 0 8px 10px 8px;
  }
  .brand-tab-inner {
    width: 100%; height: 100%;
    background: var(--ink-dark);
    border: 2px solid var(--brand-green);
    border-top: none;
    border-radius: 0 0 20px 20px;
    display: flex; flex-direction: column; align-items: center; justify-content: center;
    gap: 10px;
  }
  .brand-mark {
    width: 18px; height: 18px; background: var(--brand-green);
  }
  .brand-name {
    color: var(--brand-green);
    font-weight: 700;
    font-size: 26px;
    line-height: 1.05;
    text-align: center;
    letter-spacing: 0.5px;
  }
  .divider {
    position: absolute; left: 288px; top: 74px; width: 1px; height: 209px;
    background: var(--rule);
  }
  .contact {
    position: absolute; left: 311px; top: 104px;
    color: var(--text);
  }
  .person-name {
    color: var(--brand-green);
    font-weight: 700;
    font-size: 22px;
    line-height: 1;
    letter-spacing: 0.3px;
  }
  .person-role { font-size: 16px; margin-top: 3px; line-height: 1.1; }
  .contact-list { list-style: none; margin-top: 14px; }
  .contact-list li {
    display: flex; align-items: center; gap: 7px;
    font-size: 16px; line-height: 21px;
  }
  .contact-list svg { width: 15px; height: 15px; flex: none; }
  .accent { color: var(--brand-green); }
  .address { font-size: 16px; line-height: 21px; margin-top: 13px; font-style: normal; }

  /* Back */
  .card-back {
    top: 621px; background: var(--ink-dark);
    display: flex; align-items: center; justify-content: center; gap: 14px;
  }
  .card-back .brand-mark { width: 22px; height: 22px; }
  .card-back .brand-name { color: var(--paper); font-size: 34px; letter-spacing: 1px; }
</style>
</head>
<body>

<section class="card card-front" aria-label="Business card front">
  <div class="top-band"></div>
  <div class="brand-tab">
    <div class="brand-tab-inner">
      <span class="brand-mark"></span>
      <span class="brand-name">HALDEN<br>BUILD CO</span>
    </div>
  </div>
  <div class="divider"></div>
  <div class="contact">
    <h1 class="person-name">MARCUS DELANEY</h1>
    <p class="person-role">Managing Director</p>
    <ul class="contact-list">
      <li>
        <svg viewBox="0 0 24 24" fill="none" stroke="#2fd87a" stroke-width="2.2" stroke-linecap="round" stroke-linejoin="round"><path d="M5 3h4l2 5-2.5 1.5a11 11 0 0 0 6 6L16 13l5 2v4a2 2 0 0 1-2 2A16 16 0 0 1 3 5a2 2 0 0 1 2-2z"/><path d="M15 3a6 6 0 0 1 6 6M15 7a2 2 0 0 1 2 2"/></svg>
        044-555 018 246
      </li>
      <li>
        <svg viewBox="0 0 24 24"><rect x="1" y="5" width="22" height="14" fill="#2fd87a"/><path d="M1 5l11 8 11-8M1 19l8-7M23 19l-8-7" fill="none" stroke="#fff" stroke-width="1.5"/></svg>
        info@haldenbuild.com
      </li>
      <li>
        <svg viewBox="0 0 24 24" fill="none" stroke="#2fd87a" stroke-width="2"><circle cx="12" cy="12" r="10"/><ellipse cx="12" cy="12" rx="4.5" ry="10"/><path d="M2 12h20M4 7h16M4 17h16"/></svg>
        <span>www.<span class="accent">haldenbuild</span>.com</span>
      </li>
    </ul>
    <address class="address">218, Quarry Lane Road<br>30217, Kenmore County</address>
  </div>
</section>

<section class="card card-back" aria-label="Business card back">
  <span class="brand-mark"></span>
  <span class="brand-name">HALDEN BUILD CO</span>
</section>

</body>
</html>
```